Velmor Spire Nine Flash website

we need a website to cater to 2 aspect of the business. We have Velmor Spire Residence and Velmor Spire Office. For the office, we will get their inquire and arrange a face to face meetup to show them the office area for rent. For the residence side, it will need to be like staylane or roomvio.com. we want to allow them to book online for the date they need. We have a total of 10 different room configurations starting at $70 per night and up depending on the size of the room. example of the design is https://brisquelodge.com/

Target Market(s)

the website should have detail information on the layout, designs, and luxury of the building.

Industry/Entity Type

office and service appartment rental/lease

Coding

Coded - Design and coding required

Number of Pages Required

5+ page

Requirements
Must have
• a luxury perspective
Nice to have
• example https://brisquelodge.com/

```html
<!DOCTYPE html>
<html lang="en">
<head>
<meta charset="utf-8">
<title>Velmor Spire Nine — Home &amp; Residence</title>
<link rel="stylesheet" href="https://fonts.googleapis.com/css2?family=Signika:wght@400;600;700&family=Marcellus&display=swap">
<style>
:root{
  --stage:#c8c7c5;
  --gold:#c99a3b;
  --ink:#111;
  --muted:#444;
  --white:#fff;
  --red:#e0262b;
  --link:#1f8fd6;
  --footer:#141414;
  --overlay:rgba(30,30,30,.55);
}
*{box-sizing:border-box;margin:0;padding:0}
html,body{width:1087px;height:1200px;overflow:hidden;background:var(--stage)}
body{position:relative;font-family:'Signika',sans-serif;color:var(--ink)}
.abs{position:absolute}
.page{position:absolute;width:523px;background:var(--white);overflow:hidden;box-shadow:0 1px 4px rgba(0,0,0,.25)}
.page--home{left:15.5px;top:15.5px;height:288px}
.page--residence{left:552px;top:18px;height:1171px}
.topbar{left:0;top:0;width:100%;height:2.5px;background:var(--gold)}
.nav a{position:absolute;top:13px;font-size:6px;color:var(--ink);text-decoration:none}
.btn{position:absolute;display:flex;align-items:center;justify-content:center;border-radius:10px;font-family:'Marcellus',serif;font-size:6.5px;white-space:nowrap}
.btn--gold{background:var(--gold);color:var(--white)}
.btn--line{background:var(--white);color:var(--ink);border:1px solid var(--gold)}
.brand{position:absolute;left:38px;top:-26px;width:94px;height:94px;border-radius:50%;background:var(--white);z-index:3}
.brand span{position:absolute;left:0;right:0;top:70px;text-align:center;font-family:'Marcellus',serif;font-size:7.5px;color:var(--gold);letter-spacing:.2px;white-space:nowrap}
.hero-photo{position:absolute}
.hero-box{position:absolute;background:var(--overlay);color:var(--white);text-align:center}
.hero-box .kicker{position:absolute;left:0;right:0;font-size:9.5px}
.hero-box h1{position:absolute;left:0;right:0;font-weight:700;font-size:21px;line-height:1;white-space:nowrap}
.hero-box p{position:absolute;left:0;right:0;font-size:5.3px;font-weight:600;line-height:9.5px}
.search-card{position:absolute;left:49px;top:203px;width:425px;height:137px;background:var(--white);border-radius:10px;box-shadow:0 1px 5px rgba(0,0,0,.18)}
.field{position:absolute;border:1px solid #d9d9d9;border-radius:3px;font-family:'Marcellus',serif;color:#333}
.field small{display:block;font-size:5px;color:#888}
.field b{display:block;font-weight:400;font-size:6px}
.section-title{position:absolute;left:0;right:0;text-align:center;font-weight:700;font-size:22px;line-height:1}
.section-lead{position:absolute;left:110px;width:303px;text-align:center;font-size:5.8px;line-height:11px;color:#333}
.room{position:absolute;width:138px}
.room-photo{width:138px;height:125px}
.room h3{font-family:'Marcellus',serif;font-weight:400;font-size:8.3px;margin-top:8px;letter-spacing:.2px;color:var(--ink)}
.room .loc{display:flex;align-items:center;gap:4px;margin-top:3px;font-size:4.8px;color:var(--link)}
.room .loc u{white-space:nowrap}
.room .stars{color:var(--gold);font-size:5px;letter-spacing:.5px}
.room .price{font-family:'Marcellus',serif;color:var(--red);font-size:8px;margin-top:4px}
.ribbon{position:absolute;right:0;top:0;width:22px;height:30px;background:var(--red);color:var(--white);font-family:'Marcellus',serif;font-size:8px;text-align:center;padding-top:7px;clip-path:polygon(0 0,100% 0,100% 78%,50% 100%,0 78%)}
.review{position:absolute;width:195px}
.avatar{position:absolute;width:35px;height:35px;border-radius:50%}
.review .name{position:absolute;font-weight:600;color:var(--ink)}
.review .stars{position:absolute;color:var(--gold);font-size:5px;letter-spacing:.5px}
.review p{position:absolute;font-size:6.1px;line-height:12.3px;color:#333}
.arrow{position:absolute;width:8px;height:8px}
.footer{position:absolute;left:0;top:1047px;width:523px;height:124px;background:var(--footer);color:var(--white)}
.footer h4{position:absolute;font-weight:400;font-size:8.3px}
.footer .item{position:absolute;font-size:5.6px;display:flex;align-items:center;gap:5px;white-space:nowrap}
.footer .brandname{position:absolute;left:23px;width:120px;top:51px;text-align:center;font-family:'Marcellus',serif;font-size:7.5px;color:#e8e8e8;white-space:nowrap}
.social{position:absolute;width:10px;height:10px;border-radius:50%;background:var(--white)}
.footer .rule{position:absolute;left:49px;top:109px;width:425px;height:.6px;background:#777}
.footer .copy{position:absolute;left:0;right:0;top:113px;text-align:center;font-size:5px}
</style>
</head>
<body>

<section class="page page--home" aria-label="Velmor Spire Nine home">
  <div class="abs topbar"></div>
  <div class="brand"><span>VELMOR SPIRE NINE</span></div>
  <nav class="nav">
    <a style="left:249px">Home</a>
    <a style="left:284px">Location</a>
    <a style="left:328px">Experience</a>
    <a style="left:380px">About Us</a>
  </nav>
  <div class="btn btn--gold" style="left:424px;top:9px;width:50px;height:15.5px">Contact Us</div>

  <div class="hero-photo" role="img" aria-label="Photo of a luxury residence bedroom in grey tones" style="left:0;top:32px;width:261px;height:256px;background:linear-gradient(160deg,#8f8d8a 0%,#5d5b58 45%,#b8b5b1 100%)"></div>
  <div class="hero-photo" role="img" aria-label="Photo of a bright modern office floor with white desks" style="left:261px;top:32px;width:262px;height:256px;background:linear-gradient(170deg,#e7e7e7 0%,#c3c3c3 55%,#9d9d9d 100%)"></div>

  <div class="hero-box" style="left:120px;top:95px;width:283px;height:139px">
    <div class="kicker" style="top:28px">Welcome To</div>
    <h1 style="top:48px">Velmor Spire Nine</h1>
    <p style="top:72px">Lorem ipsum dolor sit amet, consectetur adipiscing elit, sed do eiusmod<br>tempor incididunt ut labore et dolore magna aliqua.</p>
    <div class="btn btn--gold" style="left:61px;top:98px;width:80px;height:16px">Velmor Spire Residence</div>
    <div class="btn btn--line" style="left:143px;top:98px;width:80px;height:16px;border-color:var(--white)">Velmor Spire Office</div>
  </div>
</section>

<section class="page page--residence" aria-label="Velmor Spire Residence">
  <div class="abs topbar"></div>
  <div class="brand"><span>VELMOR SPIRE NINE</span></div>
  <nav class="nav">
    <a style="left:249px;top:15px">Home</a>
    <a style="left:284px;top:15px">Location</a>
    <a style="left:328px;top:15px">Experience</a>
    <a style="left:380px;top:15px">About Us</a>
  </nav>
  <div class="btn btn--gold" style="left:424px;top:9px;width:50px;height:16px">Contact Us</div>

  <div class="hero-photo" role="img" aria-label="Photo of a dark luxury hotel bedroom with lamps and a shag rug" style="left:0;top:33px;width:523px;height:227px;background:linear-gradient(150deg,#9a9894 0%,#5f5d5a 40%,#3f3e3c 70%,#8e8b87 100%)"></div>
  <div class="hero-box" style="left:96px;top:72px;width:328px;height:124px">
    <div class="kicker" style="top:14px">Welcome To</div>
    <h1 style="top:34px;font-size:23px">Velmor Spire Residence</h1>
    <p style="top:63px">Lorem ipsum dolor sit amet, consectetur adipiscing elit, sed do<br>eiusmod tempor incididunt ut labore et dolore magna aliqua.</p>
    <div class="btn btn--gold" style="left:137px;top:94px;width:49px;height:15px">Get Started</div>
  </div>

  <div class="search-card">
    <div class="btn btn--gold" style="left:16px;top:12px;width:65px;height:16px">Overnight Stays</div>
    <div class="btn btn--line" style="left:90px;top:12px;width:66px;height:16px">Day Use Stays</div>
    <div class="field" style="left:20px;top:37px;width:393px;height:26px;display:flex;align-items:center;padding-left:12px;gap:10px">
      <svg width="9" height="9" viewBox="0 0 10 10"><circle cx="4" cy="4" r="3.2" fill="none" stroke="#888" stroke-width=".9"/><path d="M6.4 6.4 9.3 9.3" stroke="#888" stroke-width=".9"/></svg>
      <span style="font-size:6px;color:#777">Enter the type of Room</span>
    </div>
    <div class="field" style="left:20px;top:67px;width:193px;height:26px">
      <svg class="abs" style="left:13px;top:9px" width="8" height="8" viewBox="0 0 8 8"><rect x=".5" y="1" width="7" height="6.5" fill="none" stroke="#999" stroke-width=".6"/><path d="M.5 3h7" stroke="#999" stroke-width=".6"/></svg>
      <div class="abs" style="left:32px;top:7px"><b>10 MAY 2024</b><small>SUNDAY</small></div>
      <div class="abs" style="left:88px;top:6px;width:.8px;height:14px;background:#999"></div>
      <svg class="abs" style="left:106px;top:9px" width="8" height="8" viewBox="0 0 8 8"><rect x=".5" y="1" width="7" height="6.5" fill="none" stroke="#999" stroke-width=".6"/><path d="M.5 3h7" stroke="#999" stroke-width=".6"/></svg>
      <div class="abs" style="left:125px;top:7px"><b>11 MAY 2024</b><small>MONDAY</small></div>
    </div>
    <div class="field" style="left:216px;top:67px;width:196px;height:26px">
      <svg class="abs" style="left:12px;top:8px" width="11" height="9" viewBox="0 0 11 9"><circle cx="4" cy="3" r="2" fill="none" stroke="#999" stroke-width=".6"/><path d="M.6 8.5c.5-2.5 6.3-2.5 6.8 0" fill="none" stroke="#999" stroke-width=".6"/><circle cx="7.5" cy="2.8" r="1.6" fill="none" stroke="#999" stroke-width=".6"/><path d="M8 5.2c1.5.2 2.4 1.4 2.5 3" fill="none" stroke="#999" stroke-width=".6"/></svg>
      <div class="abs" style="left:29px;top:7px"><b>2 ADULTS</b><small>1 ROOM</small></div>
    </div>
    <div class="btn btn--gold" style="left:17px;top:103px;width:64px;height:15px">Search</div>
  </div>

  <h2 class="section-title" style="top:376px">Velmor Spire Residence</h2>
  <p class="section-lead" style="top:407px">Lorem ipsum dolor sit amet, consectetur adipiscing elit, sed do eiusmod tempor incididunt ut labore et dolore magna aliqua. Ut enim ad minim veniam, quis nostrud exercitation</p>

  <article class="room" style="left:49px;top:446px">
    <div class="room-photo" role="img" aria-label="Photo of a grey double bedroom with armchair" style="background:linear-gradient(170deg,#d8d6d2,#6b6864 60%,#9a968f)"></div>
    <div class="ribbon">7.9</div>
    <h3>SED UT PERSPICIATIS UNDE</h3>
    <div class="loc"><svg width="6" height="7" viewBox="0 0 6 7"><path d="M3 7C1 4.5 0 3.5 0 2.5a3 3 0 0 1 6 0C6 3.5 5 4.5 3 7z" fill="var(--red)"/><circle cx="3" cy="2.5" r="1" fill="#fff"/></svg><u>Lorem ipsum dolor sit amet, consectetur adipiscing</u></div>
    <div class="price">INR 24,437.1</div>
  </article>
  <article class="room" style="left:192px;top:446px">
    <div class="room-photo" role="img" aria-label="Photo of a white living room with fireplace" style="background:linear-gradient(170deg,#eeeeec,#bdbab5 55%,#8d7b66)"></div>
    <h3>SED UT PERSPICIATIS UNDE</h3>
    <div class="loc"><svg width="6" height="7" viewBox="0 0 6 7"><path d="M3 7C1 4.5 0 3.5 0 2.5a3 3 0 0 1 6 0C6 3.5 5 4.5 3 7z" fill="var(--red)"/><circle cx="3" cy="2.5" r="1" fill="#fff"/></svg><span class="stars">★★★★★</span><u>consectetur adipiscing</u></div>
    <div class="price">INR 22,437.1</div>
  </article>
  <article class="room" style="left:335px;top:446px">
    <div class="room-photo" role="img" aria-label="Photo of a bedroom with city view window" style="background:linear-gradient(170deg,#bdbab6,#6a6763 55%,#3a3937)"></div>
    <div class="ribbon">9.6</div>
    <h3>SED UT PERSPICIATIS UNDE</h3>
    <div class="loc"><svg width="6" height="7" viewBox="0 0 6 7"><path d="M3 7C1 4.5 0 3.5 0 2.5a3 3 0 0 1 6 0C6 3.5 5 4.5 3 7z" fill="var(--red)"/><circle cx="3" cy="2.5" r="1" fill="#fff"/></svg><u>Lorem ipsum dolor sit amet, consectetur adipiscing</u></div>
    <div class="price">INR 10,437.1</div>
  </article>
  <article class="room" style="left:49px;top:626px">
    <div class="room-photo" role="img" aria-label="Photo of a classic suite with chandelier" style="background:linear-gradient(170deg,#cfc3ad,#5a4f44 55%,#2e2a27)"></div>
    <h3>SED UT PERSPICIATIS UNDE</h3>
    <div class="loc"><svg width="6" height="7" viewBox="0 0 6 7"><path d="M3 7C1 4.5 0 3.5 0 2.5a3 3 0 0 1 6 0C6 3.5 5 4.5 3 7z" fill="var(--red)"/><circle cx="3" cy="2.5" r="1" fill="#fff"/></svg><u>Lorem ipsum dolor sit amet, consectetur adipiscing</u></div>
    <div class="price">INR 17,437.1</div>
  </article>
  <article class="room" style="left:192px;top:626px">
    <div class="room-photo" role="img" aria-label="Photo of a dark bedroom with padded headboard" style="background:linear-gradient(170deg,#3a3a3a,#1f1f1f 55%,#5c5c5c)"></div>
    <div class="ribbon">9.6</div>
    <h3>SED UT PERSPICIATIS UNDE</h3>
    <div class="loc"><svg width="6" height="7" viewBox="0 0 6 7"><path d="M3 7C1 4.5 0 3.5 0 2.5a3 3 0 0 1 6 0C6 3.5 5 4.5 3 7z" fill="var(--red)"/><circle cx="3" cy="2.5" r="1" fill="#fff"/></svg><span class="stars">★★★★★</span><u>consectetur adipiscing</u></div>
    <div class="price">INR 15,437.1</div>
  </article>
  <article class="room" style="left:335px;top:626px">
    <div class="room-photo" role="img" aria-label="Photo of a dim bedroom with round bed and warm lighting" style="background:linear-gradient(170deg,#5a4a40,#2a2320 55%,#4a4542)"></div>
    <h3>SED UT PERSPICIATIS UNDE</h3>
    <div class="loc"><svg width="6" height="7" viewBox="0 0 6 7"><path d="M3 7C1 4.5 0 3.5 0 2.5a3 3 0 0 1 6 0C6 3.5 5 4.5 3 7z" fill="var(--red)"/><circle cx="3" cy="2.5" r="1" fill="#fff"/></svg><u>Lorem ipsum dolor sit amet, consectetur adipiscing</u></div>
    <div class="price">INR 13,437.1</div>
  </article>

  <div class="btn btn--gold" style="left:229px;top:819px;width:65px;height:15px">View All</div>

  <h2 class="section-title" style="top:871px;font-size:23px">What Our Client Says?</h2>

  <svg class="arrow" style="left:17px;top:973px" viewBox="0 0 8 8"><circle cx="4" cy="4" r="4" fill="#8d8d8d"/><path d="M4.6 2.2 2.8 4l1.8 1.8M2.8 4h2.8" stroke="#fff" stroke-width=".8" fill="none"/></svg>
  <svg class="arrow" style="left:491px;top:973px" viewBox="0 0 8 8"><circle cx="4" cy="4" r="4" fill="#8d8d8d"/><path d="M3.4 2.2 5.2 4 3.4 5.8M5.2 4H2.4" stroke="#fff" stroke-width=".8" fill="none"/></svg>

  <div class="avatar" role="img" aria-label="Portrait of the reviewer" style="left:51px;top:920px;background:linear-gradient(160deg,#c9c6c2,#3b3f48)"></div>
  <div class="review" style="left:51px;top:920px">
    <div class="name" style="left:44px;top:6px;font-size:7.8px">Arvid Kessel</div>
    <div class="stars" style="left:44px;top:19px">★★★★★</div>
    <p style="left:0;top:44px;width:195px">Lorem ipsum dolor sit amet, consectetur adipiscing elit, sed do eiusmod tempor incididunt ut labore et dolore magna aliqua. Ut enim ad minim veniam, quis nostrud exercitation ullamco laboris nisi ut aliquip ex ea commodo consequat.</p>
  </div>
  <div class="abs" style="left:259px;top:955px;width:1.5px;height:52px;background:#ccc"></div>
  <div class="avatar" role="img" aria-label="Portrait of the reviewer" style="left:283px;top:920px;background:linear-gradient(160deg,#e2c8a4,#a07a58)"></div>
  <div class="review" style="left:282px;top:920px">
    <div class="name" style="left:44px;top:9px;font-size:5.8px">Mira Holt</div>
    <div class="stars" style="left:44px;top:19px">★★★★★</div>
    <p style="left:0;top:44px;width:195px">Lorem ipsum dolor sit amet, consectetur adipiscing elit, sed do eiusmod tempor incididunt ut labore et dolore magna aliqua. Ut enim ad minim veniam, quis nostrud exercitation ullamco laboris nisi ut aliquip ex ea commodo consequat.</p>
  </div>

  <footer class="footer">
    <div class="brandname">VELMOR SPIRE NINE</div>
    <div class="social" style="left:55px;top:71px"></div>
    <div class="social" style="left:71px;top:71px"></div>
    <div class="social" style="left:86px;top:71px"></div>
    <div class="social" style="left:101px;top:71px"></div>

    <h4 style="left:171px;top:22px">Quick Links</h4>
    <div class="item" style="left:173px;top:40px">Home</div>
    <div class="item" style="left:173px;top:53px">Location</div>
    <div class="item" style="left:173px;top:66px">Experience</div>
    <div class="item" style="left:173px;top:79px">About Us</div>
    <div class="item" style="left:173px;top:92px">Contact Us</div>

    <h4 style="left:281px;top:22px">Contact Info</h4>
    <div class="item" style="left:282px;top:44px"><svg width="4" height="5" viewBox="0 0 6 7"><path d="M3 7C1 4.5 0 3.5 0 2.5a3 3 0 0 1 6 0C6 3.5 5 4.5 3 7z" fill="#fff"/></svg>Harlow Quay, Ostrel -582104</div>
    <div class="item" style="left:282px;top:61px"><svg width="5" height="5" viewBox="0 0 6 6"><path d="M1 0h1.4l.6 1.6-.9.7a3.6 3.6 0 0 0 1.6 1.6l.7-.9L6 3.6V5c0 .6-.4 1-1 1A5 5 0 0 1 0 1c0-.6.4-1 1-1z" fill="#fff"/></svg>+1000 555 0142</div>
    <div class="item" style="left:282px;top:78px"><svg width="5" height="4" viewBox="0 0 6 4"><rect width="6" height="4" fill="#fff"/><path d="M0 0l3 2.2L6 0" stroke="#141414" stroke-width=".6" fill="none"/></svg>info@velmorspirenine.in</div>

    <h4 style="left:418px;top:22px">Help Links</h4>
    <div class="item" style="left:419px;top:40px">Privacy Policy</div>
    <div class="item" style="left:419px;top:53px">Terms &amp; Conditions</div>
    <div class="item" style="left:419px;top:66px">Disclaimer</div>

    <div class="rule"></div>
    <div class="copy">Copyright © 2024 Velmor Spires. All rights reserved.</div>
  </footer>
</section>

</body>
</html>
```